Bluecrest Learning Corps by graduating students from college in two years

Based on the logo design, create stationary and business cards for
Dr. Venrel T Oskamp, CEO, (541) 482-1736
and Marisa Deltoft, Respresentative, (458) 647-2208
Address: 4719 Pellham Court, Millbrook Falls, OR 97482
Incorporate elelments of the logo

Target Market(s)

USA

Font styles to use
Other font styles liked:
• match with the logo type style

```html
<!DOCTYPE html>
<html lang="en">
<head>
<meta charset="utf-8">
<title>Bluecrest Learning Corps — Business Card</title>
<link rel="stylesheet" href="https://fonts.googleapis.com/css2?family=Tinos:wght@400;700&display=swap">
<style>
  :root {
    --page-bg: #2b2b2d;
    --card-white: #ffffff;
    --brand-yellow: #f5c02c;
    --pattern-yellow: #efb928;
    --brand-navy: #272f6b;
    --ink: #1c1c1c;
  }
  * { box-sizing: border-box; margin: 0; padding: 0; }
  html, body { width: 1200px; height: 900px; overflow: hidden; }
  body {
    background: var(--page-bg);
    font-family: "Tinos", "Times New Roman", serif;
    display: flex;
    flex-direction: column;
    align-items: center;
    justify-content: center;
    gap: 50px;
  }
  .card {
    width: 630px;
    height: 360px;
    border-radius: 26px;
    position: relative;
    overflow: hidden;
  }
  .card-front { background: var(--card-white); }
  .brand-mark {
    position: absolute;
    left: 44px; top: 80px;
    width: 230px;
    display: flex; align-items: center; gap: 12px;
  }
  .brand-dot {
    flex: none;
    width: 40px; height: 40px;
    border-radius: 50%;
    background: var(--brand-yellow);
  }
  .brand-name {
    font-weight: 700;
    font-size: 24px;
    line-height: 1.15;
    color: var(--brand-navy);
  }
  .divider {
    position: absolute;
    left: 300px; top: 48px;
    width: 2px; height: 200px;
    background: var(--brand-yellow);
  }
  .contacts {
    position: absolute;
    left: 330px; top: 46px;
    right: 20px;
    display: flex; flex-direction: column; gap: 22px;
  }
  .person-name {
    font-weight: 700;
    font-size: 28px;
    color: var(--brand-yellow);
    line-height: 1.05;
    white-space: nowrap;
  }
  .person-role { font-size: 17px; color: var(--ink); margin-top: 4px; }
  .person-phone {
    font-size: 17px; color: var(--ink);
    display: flex; align-items: center; gap: 8px; margin-top: 6px;
  }
  .icon { width: 15px; height: 15px; flex: none; }
  .address {
    position: absolute;
    left: 44px; bottom: 40px;
    font-size: 17px; color: var(--ink);
    display: flex; align-items: center; gap: 8px;
  }
  .card-back { background: var(--brand-yellow); }
  .back-pattern {
    position: absolute; inset: 0;
    background: linear-gradient(135deg, var(--brand-yellow), var(--pattern-yellow));
  }
  .back-seal {
    position: absolute;
    left: 50%; top: 50%;
    transform: translate(-50%, -50%);
    display: flex; align-items: center; gap: 16px;
    width: 320px;
  }
  .back-seal .brand-dot { background: var(--brand-navy); width: 52px; height: 52px; }
  .back-seal .brand-name { font-size: 34px; }
</style>
</head>
<body>
  <section class="card card-front">
    <div class="brand-mark">
      <span class="brand-dot"></span>
      <span class="brand-name">Bluecrest Learning Corps</span>
    </div>
    <div class="divider"></div>
    <div class="contacts">
      <div class="person">
        <div class="person-name">Dr. Venrel T Oskamp</div>
        <div class="person-role">CEO</div>
        <div class="person-phone">
          <svg class="icon" viewBox="0 0 16 16" aria-hidden="true"><path fill="#f5c02c" d="M3.6 1.2l2.3 2.6-1.3 1.8c.9 2 2.3 3.4 4.2 4.3l1.8-1.3 2.6 2.3-1.2 2.4C6.8 13.3 2.6 9.1 1.3 3.3z"/></svg>
          (541) 482-1736
        </div>
      </div>
      <div class="person">
        <div class="person-name">Marisa Deltoft</div>
        <div class="person-role">Respresentative</div>
        <div class="person-phone">
          <svg class="icon" viewBox="0 0 16 16" aria-hidden="true"><path fill="#f5c02c" d="M3.6 1.2l2.3 2.6-1.3 1.8c.9 2 2.3 3.4 4.2 4.3l1.8-1.3 2.6 2.3-1.2 2.4C6.8 13.3 2.6 9.1 1.3 3.3z"/></svg>
          (458) 647-2208
        </div>
      </div>
    </div>
    <div class="address">
      <svg class="icon" viewBox="0 0 16 16" aria-hidden="true"><path fill="#f5c02c" d="M8 1a5 5 0 0 0-5 5c0 3.8 5 9 5 9s5-5.2 5-9a5 5 0 0 0-5-5zm0 7a2 2 0 1 1 0-4 2 2 0 0 1 0 4z"/></svg>
      4719 Pellham Court, Millbrook Falls, OR 97482
    </div>
  </section>

  <section class="card card-back">
    <div class="back-pattern" role="img" aria-label="Repeating pattern of graduation caps in soft tonal yellow"></div>
    <div class="back-seal">
      <span class="brand-dot"></span>
      <span class="brand-name">Bluecrest Learning Corps</span>
    </div>
  </section>
</body>
</html>
```